Business Card Design

Carl Brenton Insurance Agency, an Independent Insurance Agency which was stated on Pine Street in Laplace, Louisiana on 1958 and has grown the six locations throughout South Louisiana. We sell personal (auto Homeowners flood, liability) and commercial insurance (commercial property, general liability, workers compensation, commercial auto). I am looking for a double sided card with list the five remaining locations on the back or maybe even a folded four sided card. Our home office is a two story building with a green roof. I have had a logo designed which I have attached. Open for revisions but would like to stay with in the same green roof over an M. I have attached the logo but can not tell if I was uploaded.

Target Market(s)

Individual and commercial insurance buyers. Upper income and business owners

Industry/Entity Type

Insurance

Requirements
Must have
• Must have similar logo as uploaded. Green roof over M or something similar. List all location address and phone numbers.

Employee name, office phone number; direct phone line; email address and website list all locations on card. Very Similar colors to current logo.
Nice to have
• Possible folded card with double sided print

```html
<!DOCTYPE html>
<html lang="en">
<head>
<meta charset="utf-8">
<title>Carl Brenton Insurance Agency – Business Card</title>
<link href="https://fonts.googleapis.com/css2?family=Roboto+Condensed:wght@400;700&family=Cormorant+Garamond:wght@400&family=Arimo:wght@400&family=Open+Sans:wght@600&display=swap" rel="stylesheet">
<style>
  :root {
    --green: #1f6a45;
    --blue: #1f7cc6;
    --ink: #111111;
    --band: #000000;
    --paper: #ffffff;
    --grey-green: #5b7a68;
    --stage: #e9e6e1;
  }
  * { margin: 0; padding: 0; box-sizing: border-box; }
  html, body { width: 1200px; height: 858px; overflow: hidden; background: var(--stage); }
  .canvas { position: relative; width: 1200px; height: 858px; }

  .card {
    position: absolute;
    width: 640px; height: 366px;
    background: var(--paper);
    box-shadow: 0 6px 18px rgba(0,0,0,.18);
    overflow: hidden;
  }
  .card--front { left: 60px; top: 48px; }
  .card--back { left: 500px; top: 444px; }

  /* brand block */
  .brand { display: flex; align-items: flex-start; gap: 14px; }
  .brand__square { width: 58px; height: 58px; background: var(--blue); flex: none; margin-top: 4px; }
  .brand__name {
    font-family: "Roboto Condensed", sans-serif; font-weight: 700;
    color: var(--green); text-transform: uppercase; line-height: .98;
  }
  .brand__name span { display: block; }
  .brand__name .line-1 { font-size: 44px; letter-spacing: .5px; }
  .brand__name .line-2 { font-size: 25px; letter-spacing: .6px; }
  .tagline {
    font-family: "Roboto Condensed", sans-serif; font-weight: 700;
    color: var(--grey-green); font-size: 17px; margin-top: 3px;
  }
  .towns {
    font-family: "Open Sans", sans-serif; font-weight: 600;
    color: var(--green); font-size: 9.5px; letter-spacing: .6px; margin-top: 6px;
    white-space: nowrap;
  }

  /* front */
  .front__brand { position: absolute; left: 70px; top: 62px; }
  .front__employee {
    position: absolute; left: 142px; top: 196px;
    font-family: "Cormorant Garamond", serif; font-size: 27px;
    letter-spacing: 2px; color: var(--green); text-transform: uppercase;
  }
  .front__phones {
    position: absolute; left: 0; right: 0; bottom: 96px;
    display: flex; justify-content: space-between; padding: 0 44px;
  }
  .contact {
    display: flex; align-items: center; gap: 9px;
    font-family: "Arimo", sans-serif; font-size: 19px; color: var(--ink);
  }
  .contact svg { width: 16px; height: 16px; flex: none; }
  .front__band {
    position: absolute; left: 0; right: 0; bottom: 0; height: 76px;
    background: var(--band);
    display: flex; justify-content: space-between; align-items: center; padding: 0 44px;
  }
  .front__band .contact { color: var(--blue); }

  /* back */
  .back__band { position: absolute; left: 0; top: 0; bottom: 0; width: 74px; background: var(--band); }
  .back__stripe-green { position: absolute; right: 34px; top: 0; bottom: 0; width: 8px; background: var(--green); }
  .back__stripe-blue { position: absolute; right: 0; top: 0; bottom: 0; width: 30px; background: var(--blue); }
  .back__brand { position: absolute; left: 128px; top: 106px; }
</style>
</head>
<body>
<main class="canvas">

  <section class="card card--front" aria-label="Card front">
    <div class="brand front__brand">
      <div class="brand__square"></div>
      <div>
        <div class="brand__name"><span class="line-1">Carl Brenton</span><span class="line-2">Insurance Agency</span></div>
        <p class="tagline">Serving Pine Street Since 1964</p>
        <p class="towns">Ashford • Belmont • Cedar Bay • Dunmore • Elwood • Fairhaven</p>
      </div>
    </div>
    <p class="front__employee">Employee Name</p>

    <div class="front__phones">
      <span class="contact">
        <svg viewBox="0 0 16 16" aria-hidden="true"><rect x="1" y="5" width="14" height="10" rx="2" fill="#1f7cc6"/><path d="M3 5 Q8 0 13 5" stroke="#1f7cc6" stroke-width="2.4" fill="none"/><circle cx="8" cy="10" r="2.3" fill="#fff"/></svg>
        0750-3318204
      </span>
      <span class="contact">
        050-4400712
        <svg viewBox="0 0 16 16" aria-hidden="true"><path d="M4 1 L7 4 L5.5 6 Q7 10 10 11.5 L12 10 L15 13 L13 15 Q4 13 1 3 Z" fill="#1f7cc6"/></svg>
      </span>
    </div>

    <div class="front__band">
      <span class="contact">
        <svg viewBox="0 0 16 16" aria-hidden="true"><circle cx="8" cy="8" r="7" fill="none" stroke="#bbb" stroke-width="1.4"/><ellipse cx="8" cy="8" rx="3" ry="7" fill="none" stroke="#bbb" stroke-width="1.2"/><path d="M1 8 H15" stroke="#bbb" stroke-width="1.2"/></svg>
        www.carlbrenton.com
      </span>
      <span class="contact">
        carl@brentonagency.com
        <svg viewBox="0 0 16 16" aria-hidden="true"><rect x="1" y="3.5" width="14" height="9" fill="#fff"/><path d="M1 3.5 L8 9 L15 3.5" stroke="#000" stroke-width="1.2" fill="none"/></svg>
      </span>
    </div>
  </section>

  <section class="card card--back" aria-label="Card back">
    <div class="back__band"></div>
    <div class="back__stripe-green"></div>
    <div class="back__stripe-blue"></div>
    <div class="brand back__brand">
      <div class="brand__square"></div>
      <div>
        <div class="brand__name"><span class="line-1">Carl Brenton</span><span class="line-2">Insurance Agency</span></div>
        <p class="tagline">Serving Pine Street Since 1964</p>
        <p class="towns">Ashford • Belmont • Cedar Bay • Dunmore • Elwood • Fairhaven</p>
      </div>
    </div>
  </section>

</main>
</body>
</html>
```